Existing Website Requiring new Pages

I have an existing word press website that was built using elementor.
Website: www.tallowcrestcare.com.au
I require the Vacancies page (https://www.tallowcrestcare.com.au/vacancies/) to be modified to display our new properties along with minor tweaks to how the information is presented.
The vacancies to be displayed are the exactly the same as those that are located on the homepage of QMR website (https://qmr.org.au/)
The new pages that link off the Vacancies tab will require custom design.
There are roughly 8 pages/properties to be incorporated. i wish for the design to be very similar to that displayed in the following link; https://www.polunda.com.au/vacancies/merrylands
Along with this the back end has not been updated for the last 3 years so it also requires some maintenance.
Website is in the disability industry and the custom pages will display information relative to Property Vacancies.
I have attached a ZIP file with some design guides, the information for each of the properties (which will need to be modified to show our business name Tallowcrest Care) and the example of how it is to look based off the Polunda website.
If you guys have any suggestions or ideas on how to make this more presentable or possible i'm open to your ideas.
Target Market(s)
People looking for SDA properties custom built for people with a disability
Industry/Entity Type
Disability
Coding
Coded - Design and coding required
Number of Pages Required
5+ page

```html
<!DOCTYPE html>
<html lang="en">
<head>
<meta charset="utf-8">
<title>Vacancies – Tallowcrest Care</title>
<link href="https://fonts.googleapis.com/css2?family=Poppins:wght@300;400;500;600;700;800&display=swap" rel="stylesheet">
<style>
:root{
  --teal:#20cfa8;
  --teal-dark:#17b892;
  --pink:#ff4f8b;
  --pink-btn:#e7478f;
  --navy:#152c5b;
  --ink:#111;
  --grey:#9aa0a6;
  --text:#555;
  --bg:#f5f6f8;
  --white:#fff;
  --line:#d9d9d9;
  --dark:#222;
}
*{box-sizing:border-box;margin:0;padding:0}
html,body{width:1200px;height:3512px;overflow:hidden}
body{font-family:'Poppins',sans-serif;background:var(--bg);position:relative;color:var(--ink)}
.abs{position:absolute}
/* header */
.site-header{position:absolute;left:0;top:0;width:1200px;height:79px;background:var(--white)}
.brand{position:absolute;left:93px;top:22px;display:flex;align-items:center;gap:8px;font-size:16px;font-weight:600;color:var(--pink-btn)}
.brand i{width:14px;height:14px;border-radius:50%;background:var(--teal);display:block}
.nav a{position:absolute;top:32px;font-size:12px;font-weight:500;color:var(--ink);text-decoration:none;letter-spacing:.2px}
.nav a.active{color:#f0a24a}
/* hero */
.hero{position:absolute;left:0;top:79px;width:1200px;height:228px;background:var(--teal);border-radius:0 0 62px 62px;color:var(--white);text-align:center}
.hero h1{position:absolute;top:56px;width:100%;font-size:31px;font-weight:700}
.hero p{position:absolute;top:104px;width:100%;font-size:15px;font-weight:400}
.latest{position:absolute;top:164px;left:255px;display:flex;align-items:center;gap:9px;font-size:11px}
.latest b{font-weight:600}
.chip{background:rgba(255,255,255,.22);border-radius:12px;padding:3px 10px;font-size:10px}
.search-card{position:absolute;left:150px;top:275px;width:893px;height:63px;background:var(--white);border-radius:10px;box-shadow:0 6px 20px rgba(0,0,0,.06)}
.search-input{position:absolute;left:27px;top:13px;width:188px;height:37px;background:#f1f2f4;border-radius:6px;font-size:13px;color:var(--grey);padding:9px 12px}
.search-input svg{position:absolute;right:10px;top:11px}
.sep{position:absolute;top:20px;width:1px;height:24px;background:#e3e3e3}
.select{position:absolute;top:22px;font-size:14px;color:#555}
.select svg{position:absolute;top:5px}
.search-btn{position:absolute;left:695px;top:10px;width:189px;height:44px;background:var(--teal);border-radius:6px;color:var(--white);font-size:14px;display:flex;align-items:center;justify-content:center;gap:8px}
/* cards */
.section-title{position:absolute;left:94px;font-size:20px;font-weight:500;color:var(--ink)}
.photo{position:absolute;border-radius:8px;overflow:hidden}
.badge{position:absolute;right:0;top:0;background:var(--pink);color:var(--white);font-size:13px;padding:5px 28px;border-radius:0 8px 0 14px}
.badge b{font-weight:600}
.photo .name{position:absolute;left:20px;bottom:38px;color:var(--white);font-size:16px;font-weight:400}
.photo .loc{position:absolute;left:20px;bottom:19px;color:var(--white);font-size:12px;font-weight:300}
.tile-name{position:absolute;font-size:17px;color:var(--navy)}
.tile-loc{position:absolute;font-size:12px;color:#b0b0b0;font-weight:300}
.fade{position:absolute;left:1010px;width:78px;height:221px;background:linear-gradient(90deg,rgba(245,246,248,0),#ececec);border-radius:0 8px 8px 0}
.arrow{position:absolute;width:48px;height:48px;border-radius:50%;background:var(--white);box-shadow:0 3px 10px rgba(0,0,0,.12);display:flex;align-items:center;justify-content:center}
.load-more{position:absolute;left:490px;top:1450px;width:220px;height:45px;border:1.5px solid var(--pink-btn);border-radius:6px;color:var(--pink-btn);font-size:15px;display:flex;align-items:center;justify-content:center;background:var(--white)}
/* services */
.services-band{position:absolute;left:0;top:1561px;width:1200px;height:338px;background:var(--white);border-radius:0 0 26px 0}
.services-title{position:absolute;left:97px;top:1655px;font-size:33px;font-weight:800;line-height:48px;color:var(--ink)}
.services-title span{color:var(--teal)}
.services-intro{position:absolute;left:570px;top:1684px;width:540px;font-size:13px;color:#666;line-height:19px}
.service{position:absolute;top:1782px;width:256px;height:203px;background:var(--white);border-radius:4px;box-shadow:0 8px 24px rgba(0,0,0,.06);text-align:center}
.service svg{margin-top:26px}
.service h3{margin-top:14px;font-size:13px;font-weight:700;letter-spacing:1.2px;color:var(--ink)}
.service p{margin:10px auto 0;width:205px;font-size:13px;line-height:19px;color:#555}
/* faq */
.faq-title{position:absolute;left:0;top:2070px;width:1200px;text-align:center;font-size:41px;font-weight:700;line-height:60px}
.faq-q{position:absolute;left:84px;font-size:23px;font-weight:700;color:#222}
.faq-a{position:absolute;left:84px;top:2274px;width:1030px;font-size:15px;line-height:30px;color:#666}
.faq-line{position:absolute;left:67px;width:1066px;height:1px;background:var(--line)}
.faq-icon{position:absolute;left:1084px}
/* contact */
.contact{position:absolute;left:0;top:2686px;width:1200px;height:461px;background:linear-gradient(120deg,#3a3631,#5b544c 45%,#2f2c29)}
.contact-wave{position:absolute;left:0;top:2680px}
.contact h2{position:absolute;top:2830px;width:1200px;text-align:center;color:var(--white);font-size:49px;font-weight:700}
.contact p{position:absolute;left:300px;top:2906px;width:600px;text-align:center;color:var(--white);font-size:13px;line-height:22px}
.contact-btn{position:absolute;left:517px;top:2990px;width:166px;height:54px;background:var(--pink-btn);border-radius:5px;color:var(--white);font-size:14px;font-weight:600;display:flex;align-items:center;justify-content:center}
/* footer */
.footer{position:absolute;left:0;top:3147px;width:1200px;height:285px;background:var(--white)}
.footer-brand{position:absolute;left:97px;top:3262px;display:flex;align-items:center;gap:10px;font-size:22px;font-weight:600;color:var(--pink-btn)}
.footer-brand i{width:18px;height:18px;border-radius:50%;background:var(--teal);display:block}
.footer-contact{position:absolute;left:96px;font-size:12.5px;color:#666;display:flex;align-items:center;gap:8px}
.social{position:absolute;left:517px;width:33px;height:33px;border-radius:50%;background:#1c3a73}
.social.badge-shape{background:#6b2c91}
.col-head{position:absolute;font-size:14px;font-weight:600;color:var(--navy);border-left:3px solid #2d8fe0;padding-left:12px;line-height:14px}
.col-link{position:absolute;font-size:12.5px;color:#8a8a8a;line-height:22px;width:232px;border-bottom:1px solid #eee;padding-bottom:4px}
.bottom-bar{position:absolute;left:0;top:3432px;width:1200px;height:80px;background:var(--dark);color:#bbb;font-size:11px;text-align:center;line-height:80px}
</style>
</head>
<body>

<header class="site-header">
  <div class="brand"><i></i>Tallowcrest Care</div>
  <nav class="nav">
    <a style="left:620px">HOME</a>
    <a style="left:675px">ABOUT US</a>
    <a class="active" style="left:753px">WHAT WE DO <svg width="12" height="8" viewBox="0 0 12 8"><path d="M1 1l5 5 5-5" fill="none" stroke="#f0a24a" stroke-width="1.5"/></svg></a>
    <a style="left:871px">REFERRALS</a>
    <a style="left:952px">FEEDBACK</a>
    <a style="left:1031px">CONTACT US</a>
  </nav>
</header>

<section class="hero">
  <h1>Vacancies</h1>
  <p>Specialist Disability Accommodation (SDA)</p>
  <div class="latest"><b>Latest Search:</b>
    <span class="chip">Modern Family Home</span>
    <span class="chip">Chic Downtown Condo</span>
    <span class="chip">Cottage Near the Mountains</span>
    <span class="chip">Historic Victorian Home</span>
  </div>
</section>

<div class="search-card">
  <div class="search-input">Search...
    <svg width="15" height="15" viewBox="0 0 16 16"><circle cx="7" cy="7" r="5.5" fill="none" stroke="#333" stroke-width="1.6"/><path d="M11 11l4 4" stroke="#333" stroke-width="1.6"/></svg>
  </div>
  <span class="sep" style="left:237px"></span>
  <div class="select" style="left:267px;width:170px">Type<svg style="left:150px" width="13" height="8" viewBox="0 0 13 8"><path d="M1 1l5.5 5.5L12 1" fill="none" stroke="#333" stroke-width="1.6"/></svg></div>
  <span class="sep" style="left:466px"></span>
  <div class="select" style="left:496px;width:170px">Location<svg style="left:150px" width="13" height="8" viewBox="0 0 13 8"><path d="M1 1l5.5 5.5L12 1" fill="none" stroke="#333" stroke-width="1.6"/></svg></div>
  <div class="search-btn"><svg width="14" height="14" viewBox="0 0 16 16"><circle cx="7" cy="7" r="5.5" fill="none" stroke="#fff" stroke-width="1.8"/><path d="M11 11l4 4" stroke="#fff" stroke-width="1.8"/></svg>Search</div>
</div>

<!-- Most picked -->
<h2 class="section-title" style="top:388px">Most Picked</h2>

<div class="photo" style="left:94px;top:435px;width:319px;height:383px;background:linear-gradient(160deg,#9fc3de,#6f9fc4 50%,#5b7e68)" role="img" aria-label="Row of blue seaside townhouses">
  <span class="badge">New Property</span><span class="name">Blue Harbour Fams</span><span class="loc">Jakarta, Indonesia</span>
</div>
<div class="photo" style="left:440px;top:435px;width:320px;height:179px;background:linear-gradient(160deg,#d8b58b,#8a5a3a 55%,#4a3528)" role="img" aria-label="Thatched-roof resort lounge">
  <span class="badge"><b>Only</b> 2 Left</span><span class="name">Ocean Land</span><span class="loc">Bandung, Indonesia</span>
</div>
<div class="photo" style="left:787px;top:435px;width:319px;height:179px;background:linear-gradient(160deg,#b9cfe2,#d6d3cc 50%,#3e6f78)" role="img" aria-label="Modern villa with pool">
  <span class="badge"><b>Only</b> 2 Left</span><span class="name">Stark House</span><span class="loc">Malang, Indonesia</span>
</div>
<div class="photo" style="left:440px;top:640px;width:320px;height:178px;background:linear-gradient(160deg,#c6d7e6,#eeeeea 45%,#6f8f5e)" role="img" aria-label="White Mediterranean villa among gardens">
  <span class="badge"><b>Only</b> 2 Left</span><span class="name">Vinna Vill</span><span class="loc">Malang, Indonesia</span>
</div>
<div class="photo" style="left:787px;top:640px;width:319px;height:178px;background:linear-gradient(160deg,#a8c2de,#8a7660 55%,#5f7d4a)" role="img" aria-label="Timber house with mountains behind">
  <span class="badge"><b>Only</b> 2 Left</span><span class="name">Bobox</span><span class="loc">Medan, Indonesia</span>
</div>

<!-- Houses with beauty backyard -->
<h2 class="section-title" style="top:870px">Houses with beauty backyard</h2>
<div class="fade" style="top:901px"></div>
<div class="photo" style="left:94px;top:915px;width:218px;height:150px;background:linear-gradient(160deg,#d9c69a,#5b8a4a 60%,#c85a5a)" role="img" aria-label="Conservatory garden with flowers"><span class="badge">Popular Choice</span></div>
<div class="photo" style="left:337px;top:915px;width:219px;height:150px;background:linear-gradient(180deg,#9cc1e6,#dfe8ef 45%,#5fb3c9)" role="img" aria-label="Backyard swimming pool"></div>
<div class="photo" style="left:581px;top:915px;width:219px;height:150px;background:linear-gradient(180deg,#4a86d0,#4d7a3c 45%,#7fb14e)" role="img" aria-label="Lawn with palm trees"></div>
<div class="photo" style="left:825px;top:915px;width:220px;height:150px;background:linear-gradient(160deg,#6c8c4e,#b77a3c 50%,#7d6a52)" role="img" aria-label="Wooden cabin with deck"></div>
<div class="arrow" style="left:1026px;top:976px"><svg width="14" height="22" viewBox="0 0 14 22"><path d="M2 2l9 9-9 9" fill="none" stroke="#222" stroke-width="2"/></svg></div>
<span class="tile-name" style="left:94px;top:1079px">Tabby Town</span><span class="tile-loc" style="left:94px;top:1105px">Gunung Batu, Indonesia</span>
<span class="tile-name" style="left:337px;top:1079px">Anggana</span><span class="tile-loc" style="left:337px;top:1105px">Bogor, Indonesia</span>
<span class="tile-name" style="left:581px;top:1079px">Seattle Rain</span><span class="tile-loc" style="left:581px;top:1105px">Jakarta, Indonesia</span>
<span class="tile-name" style="left:825px;top:1079px">Wodden Pit</span><span class="tile-loc" style="left:825px;top:1105px">Wonosobo, Indonesia</span>

<!-- Hotels with large living room -->
<h2 class="section-title" style="top:1173px">Hotels with large living room</h2>
<div class="fade" style="top:1205px"></div>
<div class="photo" style="left:94px;top:1219px;width:218px;height:150px;background:linear-gradient(160deg,#e9e6e0,#cfc8bd 55%,#8a7a68)" role="img" aria-label="Bright living room with sofa"></div>
<div class="photo" style="left:337px;top:1219px;width:219px;height:150px;background:linear-gradient(160deg,#d9cdb8,#a88b6a 55%,#3d8aa0)" role="img" aria-label="Living room with staircase"></div>
<div class="photo" style="left:581px;top:1219px;width:219px;height:150px;background:linear-gradient(160deg,#e8e8e8,#b9bcbd 55%,#6e8a86)" role="img" aria-label="Open-plan living room with artwork"></div>
<div class="photo" style="left:825px;top:1219px;width:220px;height:150px;background:linear-gradient(160deg,#e6ddd0,#b79f84 55%,#6b5844)" role="img" aria-label="Living and dining area"><span class="badge">Popular Choice</span></div>
<div class="arrow" style="left:1026px;top:1276px"><svg width="14" height="22" viewBox="0 0 14 22"><path d="M2 2l9 9-9 9" fill="none" stroke="#222" stroke-width="2"/></svg></div>
<span class="tile-name" style="left:94px;top:1383px">Green Park</span><span class="tile-loc" style="left:94px;top:1409px">Tangerang, Indonesia</span>
<span class="tile-name" style="left:337px;top:1383px">Podo Wae</span><span class="tile-loc" style="left:337px;top:1409px">Madiun, Indonesia</span>
<span class="tile-name" style="left:581px;top:1383px">Silver Rain</span><span class="tile-loc" style="left:581px;top:1409px">Bandung, Indonesia</span>
<span class="tile-name" style="left:825px;top:1383px">Cashville</span><span class="tile-loc" style="left:825px;top:1409px">Kemang, Indonesia</span>

<div class="load-more">Load More</div>

<!-- Services -->
<div class="services-band"></div>
<h2 class="services-title">SEE <span>BEST SERVICES</span> FOR<br>YOUR SOLUTION</h2>
<p class="services-intro">Tallowcrest Care provides Specialist Disability Accommodation (SDA) in urban environments across Sydney with easy access to medical services and pharmacies.</p>

<div class="service" style="left:59px">
  <svg width="34" height="34" viewBox="0 0 34 34"><path d="M17 3l12 4v9c0 8-5 13-12 15C10 29 5 24 5 16V7z" fill="none" stroke="var(--teal)" stroke-width="2"/><path d="M12 17l4 4 7-8" fill="none" stroke="var(--teal)" stroke-width="2"/></svg>
  <h3>FULLY ACCESSIBLE</h3><p>A shared home environment with two other house mates for people with sensory,</p>
</div>
<div class="service" style="left:334px">
  <svg width="34" height="34" viewBox="0 0 34 34"><rect x="3" y="4" width="28" height="26" rx="4" fill="none" stroke="var(--teal)" stroke-width="2"/><path d="M8 10h18M9 24c2-6 6-8 8-8s6 2 8 8" fill="none" stroke="var(--teal)" stroke-width="2"/></svg>
  <h3>IMPROVED LIVEABILITY</h3><p>A home providing high-level physical access for people with significant</p>
</div>
<div class="service" style="left:608px">
  <svg width="34" height="34" viewBox="0 0 34 34"><circle cx="17" cy="17" r="14" fill="none" stroke="var(--teal)" stroke-width="2"/><circle cx="17" cy="14" r="5" fill="none" stroke="var(--teal)" stroke-width="2"/><path d="M8 27c3-5 15-5 18 0" fill="none" stroke="var(--teal)" stroke-width="2"/></svg>
  <h3>ROBUST</h3><p>A self-contained single occupancy villa for people with significant</p>
</div>
<div class="service" style="left:884px">
  <svg width="34" height="34" viewBox="0 0 34 34"><path d="M6 4l6 1 2 7-4 3c2 4 5 7 9 9l3-4 7 2 1 6c-14 2-26-10-24-24z" fill="none" stroke="var(--teal)" stroke-width="2"/><path d="M20 4a10 10 0 0 1 10 10M20 9a5 5 0 0 1 5 5" fill="none" stroke="var(--teal)" stroke-width="2"/></svg>
  <h3>HELP CENTER &amp; SUPPORT</h3><p>A shared home with two housemates, with 24/7 support</p>
</div>

<!-- FAQ -->
<h2 class="faq-title">Frequently Asked<br>Question</h2>
<h3 class="faq-q" style="top:2221px">What is SDA?</h3>
<svg class="faq-icon" style="top:2236px" width="30" height="3"><rect width="30" height="2.5" fill="#333"/></svg>
<p class="faq-a">Specialist Disability Accommodation (SDA) is a range of housing designed for people with extreme functional impairment or very high needs. SDA homes are constructed to be more accessible for you. They enable better or safer delivery of other supports you may need.</p>
<div class="faq-line" style="top:2363px"></div>
<h3 class="faq-q" style="top:2387px">What is SDA Funding?</h3>
<svg class="faq-icon" style="top:2390px" width="30" height="30"><path d="M15 0v30M0 15h30" stroke="#333" stroke-width="2.5"/></svg>
<div class="faq-line" style="top:2446px"></div>
<h3 class="faq-q" style="top:2471px">How do I Get SDA Funding</h3>
<svg class="faq-icon" style="top:2474px" width="30" height="30"><path d="M15 0v30M0 15h30" stroke="#333" stroke-width="2.5"/></svg>
<div class="faq-line" style="top:2529px"></div>
<h3 class="faq-q" style="top:2555px">What type of SDA funding can I access?</h3>
<svg class="faq-icon" style="top:2557px" width="30" height="30"><path d="M15 0v30M0 15h30" stroke="#333" stroke-width="2.5"/></svg>

<!-- Contact band -->
<div class="contact" role="img" aria-label="Photo of a man in sunglasses with a cane and a woman working at a table"></div>
<svg class="contact-wave" width="1200" height="40" viewBox="0 0 1200 40"><path d="M0 0h1200v14c-120 10-260 8-400 14-120 5-180-16-330-6C330 30 180 12 0 22z" fill="var(--bg)"/></svg>
<h2 class="contact h2x" style="position:absolute;top:2830px;left:0;width:1200px;text-align:center;color:#fff;font-size:49px;font-weight:700;background:none;height:auto">Get In Touch With Us!</h2>
<p style="position:absolute;left:300px;top:2906px;width:600px;text-align:center;color:#fff;font-size:13px;line-height:22px">We would love to hear you from from you regarding any concerns, questions or suggestions you may have. Please use the contact us now button to reach the Tallowcrest Care Team.</p>
<div class="contact-btn">Contact Us Now</div>

<!-- Footer -->
<footer class="footer"></footer>
<div class="footer-brand"><i></i>Tallowcrest Care</div>
<div class="footer-contact" style="top:3353px"><svg width="13" height="10" viewBox="0 0 13 10"><rect x=".7" y=".7" width="11.6" height="8.6" fill="none" stroke="var(--pink-btn)" stroke-width="1.3"/><path d="M1 1l5.5 4.5L12 1" fill="none" stroke="var(--pink-btn)" stroke-width="1.3"/></svg>Email: info@tallowcrestcare.com.au</div>
<div class="footer-contact" style="top:3376px"><svg width="13" height="13" viewBox="0 0 13 13"><path d="M2 1l3 .5 1 3-2 1.5c1 2 2.5 3.5 4.5 4.5L10 8.5l3 1-.5 3C6 13 0 7 2 1z" fill="var(--pink-btn)"/></svg>Phone: +61 0400 318 562</div>
<div class="footer-contact" style="top:3398px"><svg width="13" height="13" viewBox="0 0 13 13"><circle cx="6.5" cy="6.5" r="5.6" fill="none" stroke="var(--pink-btn)" stroke-width="1.3"/><path d="M6.5 3v3.7l2.3 1.4" fill="none" stroke="var(--pink-btn)" stroke-width="1.3"/></svg>Operating Hours: 9AM To 5PM Monday - Friday</div>

<span class="social badge-shape" style="top:3203px"></span>
<span class="social" style="top:3245px"></span>
<span class="social" style="top:3287px;background:#222"></span>
<span class="social" style="top:3329px;background:#1769b3"></span>

<div class="col-head" style="left:612px;top:3196px">ACCOMMODATION</div>
<div class="col-link" style="left:612px;top:3233px">Supported Independent Living (SIL)</div>
<div class="col-link" style="left:612px;top:3266px">Specialist Disability<br>Accommodation (SDA)</div>
<div class="col-link" style="left:612px;top:3322px">Short term Accommodation<br>(Respite)</div>
<div class="col-link" style="left:612px;top:3378px">Vacancies</div>

<div class="col-head" style="left:871px;top:3196px">WHAT WE DO</div>
<div class="col-link" style="left:871px;top:3233px">In Home Care</div>
<div class="col-link" style="left:871px;top:3266px">Social &amp; Community Services</div>
<div class="col-link" style="left:871px;top:3299px">Therapeutic Supports</div>
<div class="col-link" style="left:871px;top:3332px">Support Coordination</div>
<div class="col-link" style="left:871px;top:3365px">Home Modifications</div>

<div class="bottom-bar">© Copyright 2021 | Tallowcrest Care | All Rights Reserved.</div>

</body>
</html>
```